Business Card Design Project - del varosi group

dear Sirs

we need business card design for our group ( DEL Varosi Group ) , i have got the Logo design of our group from pixel harbor in previous , so all need details relating to our group i think available with you, as well as the the chosen logo design

we hope to provide us with business card logo that to be appropaite and satisfactory to us .

thanks

note : logo design of our group is attached .
Updates

Reason: please extend the deadline of my project for additional 15 days because i didn't received appropriate design for our gruop yet . kindly beaware that i have received 77 design till now , supossed to send me 200-250 design at least . thanks

Target Market(s)

contents

name : Kerem EL Nadiri

position : Operation Manager

Industry/Entity Type

Business

Requirements
Must have

• person name

group logo
Nice to have
• logo color matching with back background

```html
<!DOCTYPE html>
<html lang="en">
<head>
<meta charset="utf-8">
<title>DEL Varosi Group – Business Card</title>
<link rel="stylesheet" href="https://fonts.googleapis.com/css2?family=Source+Sans+3:wght@400;600;700&display=swap">
<style>
  :root {
    --backdrop: #b08a2c;
    --card-white: #ffffff;
    --brand-blue: #1f5a9c;
    --blue-deep: #1c3778;
    --blue-light: #2f8fd0;
    --gold: #c59a3a;
    --gold-light: #e0bf6a;
    --text-light: #ffffff;
  }
  html, body {
    margin: 0;
    padding: 0;
    width: 1200px;
    height: 686px;
    overflow: hidden;
    background: var(--backdrop);
    font-family: "Source Sans 3", "Myriad Pro", sans-serif;
  }
  .stage { position: relative; width: 1200px; height: 686px; }
  .card {
    position: absolute;
    width: 524px;
    height: 300px;
    background: var(--card-white);
    overflow: hidden;
    box-shadow: 2px 3px 4px rgba(0,0,0,0.35);
  }
  .card--front { left: 47px; top: 115px; }
  .card--back  { left: 619px; top: 285px; }
  .card__bg { position: absolute; inset: 0; width: 100%; height: 100%; }

  .brand {
    position: absolute;
    left: 0; right: 0;
    display: flex;
    align-items: center;
    justify-content: center;
    gap: 10px;
  }
  .brand__mark { width: 20px; height: 20px; background: currentColor; }
  .brand__name {
    font-weight: 700;
    font-size: 38px;
    letter-spacing: 1px;
    line-height: 1;
  }
  .card--front .brand { top: 68px; color: var(--brand-blue); }
  .card--back .brand  { top: 162px; color: var(--text-light); }

  .contact {
    position: absolute;
    left: 0; right: 0;
    top: 202px;
    color: var(--text-light);
    text-align: center;
  }
  .contact__person { font-size: 15px; font-weight: 700; margin-bottom: 5px; }
  .contact__role { font-size: 13px; font-weight: 600; }
  .contact__divider { display: inline-block; width: 1px; height: 13px; background: var(--text-light); margin: 0 6px; vertical-align: -1px; }
  .contact__row { font-size: 12.5px; line-height: 19px; display: flex; justify-content: center; gap: 14px; }
  .contact__item { display: inline-flex; align-items: center; gap: 2px; }
  .icon { width: 11px; height: 11px; fill: var(--text-light); }

  .web-url {
    position: absolute;
    left: 0; right: 0;
    top: 58px;
    text-align: center;
    font-size: 12px;
    font-weight: 700;
    letter-spacing: 1.5px;
    color: var(--blue-deep);
  }
  .web-url__accent { color: var(--gold); }
</style>
</head>
<body>
<div class="stage">

  <section class="card card--front" aria-label="Business card front">
    <svg class="card__bg" viewBox="0 0 524 300" preserveAspectRatio="none" aria-hidden="true">
      <defs>
        <radialGradient id="frontBlue" cx="0.5" cy="0.75" r="0.7">
          <stop offset="0" stop-color="var(--blue-light)"/>
          <stop offset="1" stop-color="var(--blue-deep)"/>
        </radialGradient>
        <linearGradient id="goldSwoosh" x1="0" x2="1">
          <stop offset="0" stop-color="var(--gold)"/>
          <stop offset="0.5" stop-color="var(--gold-light)"/>
          <stop offset="1" stop-color="var(--gold)"/>
        </linearGradient>
      </defs>
      <path d="M0 158 Q262 218 524 158 L524 300 L0 300 Z" fill="url(#frontBlue)"/>
      <path d="M8 160 Q262 204 516 155 Q262 196 8 160 Z" fill="url(#goldSwoosh)" stroke="url(#goldSwoosh)" stroke-width="3"/>
    </svg>

    <div class="brand">
      <span class="brand__mark"></span>
      <span class="brand__name">DEL VAROSI GROUP</span>
    </div>

    <div class="contact">
      <div class="contact__person">Kerem EL Nadiri <span class="contact__divider"></span> <span class="contact__role">Operation Manager</span></div>
      <div class="contact__row">
        <span class="contact__item"><svg class="icon" viewBox="0 0 24 24"><path d="M6.6 10.8a15 15 0 0 0 6.6 6.6l2.2-2.2c.3-.3.7-.4 1-.2 1.1.4 2.3.6 3.6.6.6 0 1 .4 1 1V20c0 .6-.4 1-1 1A17 17 0 0 1 3 4c0-.6.4-1 1-1h3.5c.6 0 1 .4 1 1 0 1.3.2 2.5.6 3.6.1.3 0 .7-.2 1z"/></svg>(TF)123-456-7890</span>
        <span class="contact__item"><svg class="icon" viewBox="0 0 24 24"><path d="M6.6 10.8a15 15 0 0 0 6.6 6.6l2.2-2.2c.3-.3.7-.4 1-.2 1.1.4 2.3.6 3.6.6.6 0 1 .4 1 1V20c0 .6-.4 1-1 1A17 17 0 0 1 3 4c0-.6.4-1 1-1h3.5c.6 0 1 .4 1 1 0 1.3.2 2.5.6 3.6.1.3 0 .7-.2 1z"/></svg>123-456-7890</span>
        <span class="contact__item"><svg class="icon" viewBox="0 0 24 24"><path d="M6 2h10l2 2v5H6zM3 10h18v9h-3v3H6v-3H3zm5 6v4h8v-4z"/></svg>123-456-7890</span>
      </div>
      <div class="contact__row">
        <span class="contact__item"><svg class="icon" viewBox="0 0 24 24"><path d="M2 5h20v14H2zm2 2v1l8 5 8-5V7l-8 5z"/></svg>name@website.com</span>
        <span class="contact__item"><svg class="icon" viewBox="0 0 24 24"><path d="M12 2a10 10 0 1 0 0 20 10 10 0 0 0 0-20zm6.9 9h-3a15 15 0 0 0-1.3-6A8 8 0 0 1 18.9 11zM12 4c.9 1.2 1.8 3.6 1.9 7h-3.8c.1-3.4 1-5.8 1.9-7zM9.4 5a15 15 0 0 0-1.3 6h-3A8 8 0 0 1 9.4 5zM5.1 13h3a15 15 0 0 0 1.3 6A8 8 0 0 1 5.1 13zM12 20c-.9-1.2-1.8-3.6-1.9-7h3.8c-.1 3.4-1 5.8-1.9 7zm2.6-1a15 15 0 0 0 1.3-6h3a8 8 0 0 1-4.3 6z"/></svg>www.website.com</span>
      </div>
      <div class="contact__row">Street name City, State, zip code</div>
    </div>
  </section>

  <section class="card card--back" aria-label="Business card back">
    <svg class="card__bg" viewBox="0 0 524 300" preserveAspectRatio="none" aria-hidden="true">
      <defs>
        <radialGradient id="backBlue" cx="0.5" cy="0.55" r="0.65">
          <stop offset="0" stop-color="var(--blue-light)"/>
          <stop offset="1" stop-color="var(--blue-deep)"/>
        </radialGradient>
      </defs>
      <path d="M0 100 Q262 160 524 100 L524 300 L0 300 Z" fill="url(#backBlue)"/>
    </svg>

    <div class="web-url">www.<span class="web-url__accent">website</span>.com</div>

    <div class="brand">
      <span class="brand__mark"></span>
      <span class="brand__name">DEL VAROSI GROUP</span>
    </div>
  </section>

</div>
</body>
</html>
```